Im open to ideas.. I was thinking on my business cards aswell as my logo. a place for my name. email. phone number and abn..

ive attched a file with my business logo. which i dont love the colours.. i was think a dark background with charcoal letters so something along those colour schumes but im open to ideas..

BRM Constructions

```html
<!DOCTYPE html>
<html lang="en">
<head>
<meta charset="utf-8">
<title>BRM Constructions – Business Card</title>
<link href="https://fonts.googleapis.com/css2?family=Montserrat:wght@400;500;700;800&display=swap" rel="stylesheet">
<style>
  :root {
    --backdrop: #e9e7e4;
    --card: #ffffff;
    --brand-red: #e31b23;
    --charcoal: #2a2a2a;
    --rule: #3a3a3a;
  }
  * { margin: 0; padding: 0; box-sizing: border-box; }
  html, body {
    width: 1200px;
    height: 913px;
    overflow: hidden;
    background: var(--backdrop);
    font-family: "Montserrat", sans-serif;
  }
  .canvas {
    position: relative;
    width: 1200px;
    height: 913px;
    display: flex;
    align-items: center;
    justify-content: center;
  }
  .business-card {
    position: relative;
    width: 1000px;
    height: 571px;
    background: var(--card);
    box-shadow: 0 18px 40px rgba(0,0,0,0.18), 0 2px 6px rgba(0,0,0,0.08);
    overflow: hidden;
  }
  .accent-band {
    position: absolute;
    top: 0;
    bottom: 0;
    left: 100px;
    width: 72px;
    background: var(--brand-red);
  }
  .card-details {
    position: absolute;
    top: 70px;
    right: 70px;
    text-align: right;
    color: var(--charcoal);
  }
  .brand-name {
    display: flex;
    align-items: center;
    justify-content: flex-end;
    gap: 14px;
    font-size: 34px;
    font-weight: 800;
    letter-spacing: 1px;
    color: var(--charcoal);
    text-transform: uppercase;
    margin-bottom: 24px;
  }
  .brand-mark {
    width: 22px;
    height: 22px;
    background: var(--brand-red);
  }
  .name-block {
    width: 430px;
    margin: 0 0 20px auto;
  }
  .person-name {
    font-size: 34px;
    font-weight: 500;
    color: var(--brand-red);
    text-transform: uppercase;
    letter-spacing: 1px;
    line-height: 1.1;
    text-align: left;
  }
  .name-rule {
    margin-top: 6px;
    border-top: 2px solid var(--rule);
  }
  .job-title {
    display: block;
    margin-top: 4px;
    font-size: 17px;
    font-weight: 400;
    line-height: 1.2;
    color: var(--charcoal);
    text-align: right;
  }
  .contact-list { list-style: none; }
  .contact-list li {
    display: flex;
    align-items: center;
    justify-content: flex-end;
    gap: 10px;
    font-size: 21px;
    font-weight: 400;
    line-height: 1.55;
  }
  .contact-label,
  .highlight { color: var(--brand-red); }
  .contact-icon {
    width: 18px;
    height: 18px;
    flex: none;
  }
  .icon-spacer { width: 18px; flex: none; }
</style>
</head>
<body>
<main class="canvas">
  <article class="business-card">
    <div class="accent-band"></div>

    <section class="card-details">
      <div class="brand-name"><span class="brand-mark"></span>BRM Constructions</div>

      <div class="name-block">
        <h1 class="person-name">Marcus Hale</h1>
        <div class="name-rule"></div>
        <span class="job-title">Director</span>
      </div>

      <ul class="contact-list">
        <li><span><span class="contact-label">ABN</span>: 12 608 441 390</span><span class="icon-spacer"></span></li>
        <li>+61 400 218 735
          <svg class="contact-icon" viewBox="0 0 24 24" fill="none" stroke="var(--brand-red)" stroke-width="2.2" stroke-linecap="round" stroke-linejoin="round">
            <path d="M5 3h4l2 5-2.5 1.5a11 11 0 0 0 6 6L16 13l5 2v4a2 2 0 0 1-2 2A17 17 0 0 1 3 5a2 2 0 0 1 2-2z"/>
          </svg>
        </li>
        <li>info@brmconstructions.com
          <svg class="contact-icon" viewBox="0 0 24 24" fill="none" stroke="var(--brand-red)" stroke-width="2.2" stroke-linejoin="round">
            <rect x="3" y="5" width="18" height="14" rx="2"/>
            <path d="M3 7l9 6 9-6"/>
          </svg>
        </li>
        <li><span>www.<span class="highlight">brmconstructions</span>.com</span>
          <svg class="contact-icon" viewBox="0 0 24 24" fill="none" stroke="var(--brand-red)" stroke-width="2">
            <circle cx="12" cy="12" r="9"/>
            <path d="M3 12h18M12 3c3 3 3 15 0 18M12 3c-3 3-3 15 0 18"/>
          </svg>
        </li>
      </ul>
    </section>
  </article>
</main>
</body>
</html>
```